Website for Barlow Fabrication & Building Ltd

General Note to all.

1. Piling and gas works are separate areas of work and should not be put together.
- the marine section should really be the piling works and should have all the barges/water piles etc.
- the gas section should have the big silo looking thing

2. I would like to add in Specialist Onsite Labour and Management in the 'our services' section. The would include the Supervisors, Coded Welders, Site Fitters and Crane and Rig Crews etc.

3. I did like it how someone had use the BFB header logo as the top of the webpage with the individual tabs above and the website starting below. Please remove the VAT number and phone number from this section.

4. I also liked how one designer incorporate the orange line with spark (from the logo) as a page separator representing the welding part of the business

5. Add in a Mission Statement - To go above and beyond in to ensure our clients projects are delivered safely, ahead of schedule, in any environment for the benefit of not only our customers but also our employees and communities we work in.

6. Add in Business Objectives -BFB is on a mission to be one of the leading contractors in UK to supply All Site Labour - ranging from Site Management, fully Coded Welders, Site Fitters and Crane and Rig Crews.

7. I am happy for you to add in photos that are not ours for the thumbs nails for the our services. ie a colourful welding pics/cool tunnelling pic etc - just make sure I will not get done for copy write infringements

8. I would like a some type of 'contact us' field or 'request a consultation' section.

9. Please confirm if the webpages you create will be compatible for both desktop and mobile app and how difficult it will be to update personally once it is live.

10. You have all done very well and have thus far been very impressed with what you have produced. I gave a very vague brief as I was not entirely sure how you would go about making something with very little information. Some of the designs look very professional.

11. I'm not sure how once I choose the winning design how that then transfers over to my domain? Perhaps someone can help me with that? I will also be looking for a web hosting platform so feel free to provide this information.

After using Sketch hive for successful getting a professional logo for the company I'm giving the web design option a go.

I am looking for a professional website for the above civil construction company.

The company director has many years experience in Marine, tunnelling, conveyors, stadium construction gas and piling works including piling works for coal ports, bridges and tunnels.

The company currently provide 20+ skilled and experienced guys from all trades (supervisors, coded welders, fitters, crane drivers and crane supervisors, rigglers, slingers and piling operatives) on the Corran Shoreline project in London - London's new super sewer. Most of this work is off barges carrying cranes (upto 600T and drill rigs).

As we are looking to expand and get more subcontracts we need a web presence to say who we are and what we do.

I'll include the 2 company logos we currently use below

I have included an info doc with pics you may or may not use.

Target Market(s)

Mainly other large construction companies and potential subcontractors

Industry/Entity Type

Construction Company

Coding

Coded - Design and coding required

Font styles to use
Sans Serif

Colors
0655a3
f37122
ffffff

Requirements
Must have
• Few tabs
• Simple to use/update but still professional look
• The challenge will be making the website look professional with not much available content.
Should not have
• No residential house building

```html
<!DOCTYPE html>
<html lang="en">
<head>
<meta charset="utf-8">
<title>Barlow Fabrication &amp; Building</title>
<link href="https://fonts.googleapis.com/css2?family=Roboto:wght@400;500;700&family=Open+Sans:wght@400;600&display=swap" rel="stylesheet">
<style>
:root{
  --blue:#0655a3;
  --navy:#123a78;
  --orange:#f37122;
  --white:#ffffff;
  --ink:#222222;
  --muted:#555555;
  --black:#121212;
  --line:#cfcfcf;
}
*{box-sizing:border-box;margin:0;padding:0}
html,body{width:1200px;height:3093px;overflow:hidden}
body{position:relative;background:var(--white);font-family:"Open Sans",Arial,sans-serif;color:var(--ink)}
.abs{position:absolute}
.heading{font-family:"Roboto",Arial,sans-serif;font-weight:700;text-transform:uppercase}

/* header */
.topbar{top:0;left:0;width:1200px;height:95px;background:var(--white);z-index:3}
.contact-line{top:14px;right:95px;font-size:15px;color:var(--ink);display:flex;gap:12px;align-items:center}
.contact-line svg{fill:var(--orange);width:14px;height:14px;margin-right:6px;vertical-align:-2px}
.nav{top:55px;right:95px;display:flex;gap:30px;font-family:"Roboto",Arial,sans-serif;font-weight:500;font-size:15px;text-transform:uppercase;align-items:center}
.nav .active{color:var(--orange)}
.brand{top:6px;left:90px;width:190px;height:164px;border-radius:50%;background:var(--white);z-index:4;display:flex;flex-direction:column;align-items:center;justify-content:center;border:6px solid var(--white);box-shadow:0 0 0 4px var(--blue) inset}
.brand-name{font-family:"Roboto",Arial,sans-serif;font-weight:700;font-size:44px;color:var(--navy);line-height:1}
.brand-sub{font-family:"Roboto",Arial,sans-serif;font-weight:700;font-size:9px;color:var(--navy);text-transform:uppercase;margin-top:4px}

/* hero */
.hero{top:95px;left:0;width:1200px;height:620px;background:linear-gradient(180deg,#4a4f5a 0%,#6a5a4a 45%,#3b3a3a 75%,#2a2a2e 100%)}
.hero-copy{top:255px;left:0;width:1200px;text-align:center;color:var(--white);z-index:2}
.hero-title{font-size:50px;letter-spacing:.5px}
.hero-sub{font-size:24px;margin-top:18px}
.btn-outline{display:inline-block;border:2px solid var(--white);border-radius:26px;color:var(--white);font-family:"Roboto",Arial,sans-serif;font-weight:700;font-size:16px;text-transform:uppercase;padding:13px 28px}
.hero .btn-outline{margin-top:38px}
.dots{top:618px;left:0;width:1200px;display:flex;justify-content:center;gap:6px;z-index:2}
.dots span{width:13px;height:13px;border-radius:50%;border:2px solid var(--white)}
.dots span.on{background:var(--white)}
.hero-curve{top:540px;left:0;z-index:2}

/* welcome */
.welcome-box{top:783px;left:97px;width:604px;height:407px;border:1px solid var(--line)}
.welcome-title{top:828px;left:131px;font-size:35px;line-height:46px;color:var(--ink)}
.welcome-text{top:938px;left:131px;width:460px;font-size:13.5px;line-height:27px;color:var(--muted)}
.btn-fill{display:inline-block;background:var(--orange);color:var(--white);border-radius:24px;font-family:"Roboto",Arial,sans-serif;font-weight:700;font-size:15px;text-transform:uppercase;text-align:center}
.read-more{top:1097px;left:134px;width:130px;height:44px;line-height:44px}
.video{top:825px;left:619px;width:482px;height:323px;background:linear-gradient(180deg,#5c7fb0 0%,#8a8f8c 55%,#3c5a6e 100%);box-shadow:0 2px 8px rgba(0,0,0,.25)}
.play{top:957px;left:830px;width:60px;height:60px;border-radius:50%;border:3px solid var(--white);background:rgba(0,0,0,.55)}

/* projects */
.projects{top:1274px;left:0;width:1200px;height:709px;background:linear-gradient(135deg,#0a4a98 0%,var(--blue) 50%,#0b4790 100%)}
.section-title{left:0;width:1200px;text-align:center;font-size:32px}
.projects .section-title{top:80px;color:var(--white)}
.grid{top:140px;left:99px;display:grid;grid-template-columns:repeat(4,243px);grid-auto-rows:198px;gap:14px 10px}
.tile{border:3px solid var(--white)}
.t1{background:linear-gradient(180deg,#6a8a6a,#3e3a30)}
.t2{background:linear-gradient(180deg,#4d86d6,#2b2b2b)}
.t3{background:linear-gradient(180deg,#3f74c9,#b88a2c)}
.t4{background:linear-gradient(180deg,#8fb3e0,#7a6a58)}
.t5{background:linear-gradient(180deg,#8a9aa6,#3a3a32)}
.t6{background:linear-gradient(180deg,#4a8ad8,#3c4a4e)}
.t7{background:linear-gradient(180deg,#6a9ad6,#5a4a3a)}
.t8{background:linear-gradient(180deg,#c2cbd6,#2e2e30)}
.view-more{top:588px;left:526px;width:148px;height:51px;line-height:47px;text-align:center;padding:0}

/* contact */
.contact{top:1983px;left:0;width:1200px;height:425px;background:linear-gradient(180deg,#3a4150 0%,#5a5050 55%,#2a2626 100%)}
.contact .section-title{top:62px;color:var(--white)}
.field{background:var(--white);font-size:11px;color:var(--muted);padding:7px 10px}
.f-name{top:134px;left:285px;width:309px;height:33px}
.f-phone{top:134px;left:604px;width:309px;height:33px}
.f-email{top:180px;left:285px;width:628px;height:33px}
.f-msg{top:225px;left:285px;width:628px;height:81px}
.submit{top:324px;left:542px;width:116px;height:43px;line-height:43px}

/* partners */
.partners .section-title{top:2484px;color:var(--ink)}
.partner{top:2561px;width:190px;height:99px;border:1px solid var(--line);display:flex;align-items:center;justify-content:center;font-family:"Roboto",Arial,sans-serif;font-weight:700;font-size:20px;color:var(--navy)}
.arrow{top:2590px;width:40px;height:40px;border-radius:50%;border:1px solid var(--line);display:flex;align-items:center;justify-content:center}
.arrow svg{width:14px;height:14px;stroke:var(--ink);fill:none;stroke-width:2}

/* footer */
.footer-curve{top:2740px;left:0}
.social{top:2863px;left:0;width:1200px;display:flex;justify-content:center;gap:10px}
.social span{width:48px;height:48px;border-radius:50%;border:2px solid var(--white)}
.footer-info{top:2948px;left:0;width:1200px;display:flex;justify-content:center;gap:16px;color:var(--white);font-size:14px;align-items:center}
.footer-info svg{fill:var(--white);width:13px;height:13px;margin-right:6px;vertical-align:-2px}
.footer-links{top:2988px;left:0;width:1200px;text-align:center;color:var(--white);font-size:13px;word-spacing:4px}
.copyright{top:3025px;left:0;width:1200px;text-align:center;color:var(--white);font-size:13px}
</style>
</head>
<body>

<header class="abs topbar">
  <div class="abs contact-line">
    <span><svg viewBox="0 0 24 24"><path d="M6.6 10.8a15 15 0 0 0 6.6 6.6l2.2-2.2a1 1 0 0 1 1-.25 11.4 11.4 0 0 0 3.6.57 1 1 0 0 1 1 1V20a1 1 0 0 1-1 1A17 17 0 0 1 3 4a1 1 0 0 1 1-1h3.5a1 1 0 0 1 1 1c0 1.25.2 2.45.57 3.57a1 1 0 0 1-.25 1z"/></svg>0800 555 0142</span>
    <span>|</span>
    <span><svg viewBox="0 0 24 24"><path d="M2 5h20v14H2z M2 5l10 8 10-8" /></svg>info@barlowfabrication.co.uk</span>
  </div>
  <nav class="abs nav">
    <span class="active">Home</span><span>About Us</span><span>Services</span><span>Project</span><span>Blog</span><span>Contact Us</span>
    <svg width="16" height="16" viewBox="0 0 24 24" fill="none" stroke="#222" stroke-width="3"><circle cx="10" cy="10" r="7"/><path d="M15 15l7 7"/></svg>
  </nav>
</header>

<div class="abs brand">
  <div class="brand-name">BFB</div>
  <div class="brand-sub">Barlow Fabrication &amp; Building</div>
</div>

<section class="abs hero" role="img" aria-label="Welders in orange workwear on a scaffolded piling platform over the river at dusk">
</section>
<div class="abs hero-copy">
  <h1 class="heading hero-title">Barlow Fabrication &amp; Building</h1>
  <p class="hero-sub">Over 15years experience working in the civil construction industry</p>
  <span class="btn-outline">Get More Info</span>
</div>
<div class="abs dots"><span class="on"></span><span></span><span></span><span></span></div>
<svg class="abs hero-curve" width="1200" height="200" viewBox="0 0 1200 200">
  <path d="M0 40 Q620 230 1200 10 Q620 270 0 80 Z" fill="var(--orange)"/>
  <path d="M0 80 Q620 270 1200 10 L1200 200 L0 200 Z" fill="var(--white)"/>
  <path d="M0 40 Q620 230 1200 10 L1200 0 L1200 30 Q620 215 0 60 Z" fill="var(--white)"/>
</svg>

<section class="welcome">
  <div class="abs welcome-box"></div>
  <h2 class="abs heading welcome-title">Welcome to Barlow<br>Fabrication &amp; Building</h2>
  <p class="abs welcome-text">Barlow Fabrication &amp; Building has over 15years experience working in the civil construction industry. We are currently working on the Corran Shoreline project in London. We are subcontracted to Harwick Delmont Joint Venture and provide a highly skilled workforce across many of the Corran Shoreline sites.</p>
  <span class="abs btn-fill read-more">Read More</span>
  <div class="abs video" role="img" aria-label="Video still of a piling barge with scaffolding on the river"></div>
  <div class="abs play"><svg width="54" height="54" viewBox="0 0 54 54"><path d="M21 16 L38 27 L21 38 Z" fill="#fff"/></svg></div>
</section>

<section class="abs projects">
  <h2 class="abs heading section-title">Our Projects</h2>
  <div class="abs grid">
    <div class="tile t1" role="img" aria-label="Steel piles with green rig"></div>
    <div class="tile t2" role="img" aria-label="Sheet pile wall under blue sky"></div>
    <div class="tile t3" role="img" aria-label="Crane and drill rig on barge"></div>
    <div class="tile t4" role="img" aria-label="Piling platform on the river"></div>
    <div class="tile t5" role="img" aria-label="Rig mast beside steel casing"></div>
    <div class="tile t6" role="img" aria-label="Barges and cranes on the river"></div>
    <div class="tile t7" role="img" aria-label="Scaffolded platform over water"></div>
    <div class="tile t8" role="img" aria-label="Steel piles in the river"></div>
  </div>
  <span class="abs btn-outline view-more">View More</span>
</section>

<section class="abs contact" role="img" aria-label="Crew working beneath a crane at dusk">
  <h2 class="abs heading section-title">Contact Us</h2>
  <div class="abs field f-name">Name :</div>
  <div class="abs field f-phone">Phone no :</div>
  <div class="abs field f-email">Email :</div>
  <div class="abs field f-msg">Message :</div>
  <span class="abs btn-fill submit">Submit</span>
</section>

<section class="partners">
  <h2 class="abs heading section-title">Worked With</h2>
  <div class="abs arrow" style="left:30px"><svg viewBox="0 0 14 14"><path d="M9 2 L4 7 L9 12"/></svg></div>
  <div class="abs partner" style="left:99px">Shoreline</div>
  <div class="abs partner" style="left:302px">Kestrel JV</div>
  <div class="abs partner" style="left:505px">Norvale</div>
  <div class="abs partner" style="left:708px">Aldane</div>
  <div class="abs partner" style="left:911px">Greyford</div>
  <div class="abs arrow" style="left:1130px"><svg viewBox="0 0 14 14"><path d="M5 2 L10 7 L5 12"/></svg></div>
</section>

<footer>
  <svg class="abs footer-curve" width="1200" height="353" viewBox="0 0 1200 353">
    <path d="M0 95 Q600 -40 1200 80 Q600 5 0 140 Z" fill="var(--orange)"/>
    <path d="M0 140 Q600 5 1200 80 L1200 353 L0 353 Z" fill="var(--black)"/>
  </svg>
  <div class="abs social" aria-label="Social links"><span></span><span></span><span></span><span></span></div>
  <div class="abs footer-info">
    <span><svg viewBox="0 0 24 24"><path d="M12 2a7 7 0 0 0-7 7c0 5 7 13 7 13s7-8 7-13a7 7 0 0 0-7-7zm0 9.5A2.5 2.5 0 1 1 12 6.5a2.5 2.5 0 0 1 0 5z"/></svg>Finibus Bonorum et Maloru</span>
    <span>|</span>
    <span><svg viewBox="0 0 24 24"><path d="M6.6 10.8a15 15 0 0 0 6.6 6.6l2.2-2.2a1 1 0 0 1 1-.25 11.4 11.4 0 0 0 3.6.57 1 1 0 0 1 1 1V20a1 1 0 0 1-1 1A17 17 0 0 1 3 4a1 1 0 0 1 1-1h3.5a1 1 0 0 1 1 1c0 1.25.2 2.45.57 3.57a1 1 0 0 1-.25 1z"/></svg>0800 555 0142</span>
    <span>|</span>
    <span><svg viewBox="0 0 24 24"><path d="M2 5h20v14H2z"/></svg>info@barlowfabrication.co.uk</span>
  </div>
  <p class="abs footer-links">Help | FAQ | Support | Sitemap | Terms Of Use | Privacy Statement</p>
  <p class="abs copyright">Copyrights © 2018, Barlow Fabrication &amp; Building. All rights reserved.</p>
</footer>

</body>
</html>
```